KVM Contracting services . Building and maintenance services, optic fibre installation

Business cards and logo design.I need a logo that I can use on business cards ,workwear and on my vehicles. I would like the KVM to be the main or larger text and contracting services to be the smaller or less important text.I like monograms, modern designs and repeating patterns symbols. I am also a Gemini and my favourite number is 22 so if this can be any inspiration to help with the design. Am thinking of the using German flag colours as a his is my family’s heritage. And the other 2 main colours I wear is black and white.But any ideas are appreciated.I do not need a design that is trade specific but a design that could be used for any business.

Target Market(s)

General public

Contact Information for Business Card

KVM Contracting Services ( front of business card)

(Back of business card)
Darren Holtwick
0451907326
Maintenance services
Optic fibre and data installation

Logo Text

Logo can just be pattern or monogram or incorporate KVM . I like the gemini star sign and the number 22

Colors
ec1f27
000000
fbee3e
ffffff

Requirements
Must have
• Logo and KVM Contracting Services on the front of business card
Nice to have
• Possible use of German flag colours.
• Modern design.
• Design to be able to be used on black or white background as I want to put it on clothing

```html
<!DOCTYPE html>
<html lang="en">
<head>
<meta charset="utf-8">
<title>KVM Contracting Services – Business Cards</title>
<link rel="stylesheet" href="https://fonts.googleapis.com/css2?family=Roboto:wght@400;500&family=Montserrat:wght@700&display=swap">
<style>
  :root {
    --red: #ec1f27;
    --black: #141414;
    --white: #ffffff;
    --ink: #1c1c1c;
    --rule: #555555;
    --backdrop: #5c5c5c;
  }
  * { margin: 0; padding: 0; box-sizing: border-box; }
  html, body {
    width: 1200px;
    height: 802px;
    overflow: hidden;
    background: var(--backdrop);
  }
  .canvas {
    position: relative;
    width: 1200px;
    height: 802px;
  }
  .card {
    position: absolute;
    top: 274px;
    width: 443px;
    height: 264px;
    box-shadow: 0 3px 8px rgba(0,0,0,0.35);
  }
  .card--back {
    left: 136px;
    background: var(--white);
    font-family: "Roboto", Arial, sans-serif;
    text-align: center;
    color: var(--ink);
  }
  .card--front {
    left: 624px;
    background: var(--black);
  }
  .contact-name {
    position: absolute;
    top: 82px;
    left: 0;
    width: 100%;
    font-size: 19px;
    font-weight: 500;
    color: var(--red);
  }
  .contact-phone {
    position: absolute;
    top: 107px;
    left: 0;
    width: 100%;
    font-size: 19px;
    font-weight: 400;
    letter-spacing: 0.3px;
  }
  .contact-rule {
    position: absolute;
    top: 144px;
    left: 145px;
    width: 153px;
    height: 1px;
    background: var(--rule);
  }
  .service-list {
    position: absolute;
    top: 162px;
    left: 0;
    width: 100%;
    list-style: none;
    font-size: 14px;
    line-height: 18px;
  }
  .brand {
    position: absolute;
    top: 92px;
    left: 100px;
    display: flex;
    align-items: center;
    gap: 16px;
    color: var(--red);
    font-family: "Montserrat", Arial, sans-serif;
    font-weight: 700;
  }
  .brand-dot {
    width: 70px;
    height: 70px;
    border-radius: 50%;
    background: var(--red);
    flex: none;
  }
  .brand-name {
    display: flex;
    flex-direction: column;
  }
  .brand-initials {
    font-size: 62px;
    line-height: 56px;
    letter-spacing: 8px;
  }
  .brand-tagline {
    font-size: 12.5px;
    line-height: 16px;
    letter-spacing: 0.2px;
    text-transform: uppercase;
  }
</style>
</head>
<body>
  <main class="canvas">
    <section class="card card--back" aria-label="Business card, contact side">
      <p class="contact-name">DARREN HOLTWICK</p>
      <p class="contact-phone">0451907326</p>
      <div class="contact-rule"></div>
      <ul class="service-list">
        <li>MAINTENANCE SERVICES</li>
        <li>OPTIC FIBRE AND DATA INSTALLATION</li>
      </ul>
    </section>

    <section class="card card--front" aria-label="Business card, brand side">
      <div class="brand">
        <span class="brand-dot"></span>
        <p class="brand-name">
          <span class="brand-initials">KVM</span>
          <span class="brand-tagline">Contracting Services</span>
        </p>
      </div>
    </section>
  </main>
</body>
</html>
```